Diverse, up-scale salon needs eye-catching, unique business cards.

We are looking for a unique business card design for our stylist but that can also be multi functional and used for appointment reminder and referrals. I will need a design in a format that I can modify names and titles going forward. In the past we have had a dark background with the logo on one side, and stylist and contact information on the other but we are open to all ideas. I have included our mission statement as well as branded colors below. The statement doesn't need to go on the card, it's just a reference for target market. We need space for the stylists name, title, instagram handle and then the salons phone number, website and address. I am also open to adding a spot for a qr code linked to the stylist instagram or the salon booking link.

primary brand colors:
#333333 #233415 #36502a #93874a #000000
Mission statement:
Vessolin Hair Studio, a high-end salon located in the lively Downtown Farmington, Michigan, is committed to providing exceptional services in a welcoming and relaxed environment to meet the needs of our diverse clientele.
Our salon specializes in contemporary custom haircuts, coloring, extensions, and barbering and beard grooming services. Our team of skilled stylists is passionate and inventive in their hair styling techniques. At the heart of our salon are values centered on quality, innovation, creativity, and above all, comfort. These core values are evident in every appointment across our customizable array of services.
Our goal is to establish a benchmark for exceptional hair care for every human.
Website: www.vessolinhairstudio.example
instagram: @vessolinhairstudio
address: 41782 Pelham Crest Rd, Farmington MI
phone: 248-613-4087

Industry/Entity Type

Hair Salon

Contact Information for Business Card

Stylist name, title, phone, instagram, website, address, (optional qr code)

Requirements
Should not have
• Does not need mission statement on the card.

```html
<!DOCTYPE html>
<html lang="en">
<head>
<meta charset="utf-8">
<title>Vessolin Hair Studio — Business Card</title>
<link rel="stylesheet" href="https://fonts.googleapis.com/css2?family=Arimo:wght@400;700&family=Oswald:wght@500&display=swap">
<style>
  :root {
    --olive: #93874a;
    --white: #ffffff;
    --grey-text: #7a7a7a;
    --grey-swoosh: #858585;
    --backdrop: #1f1f1f;
  }
  * { box-sizing: border-box; margin: 0; padding: 0; }
  html, body { width: 1200px; height: 1059px; overflow: hidden; background: var(--backdrop); }
  body { position: relative; font-family: "Arimo", Arial, sans-serif; }

  .card { position: absolute; overflow: hidden; }
  .card-front { left: 258px; top: 89px; width: 689px; height: 394px; background: var(--white); }
  .card-back  { left: 252px; top: 541px; width: 701px; height: 400px; background: var(--olive); }

  .front-wave { position: absolute; left: 0; top: 0; width: 689px; height: 394px; }

  .brand-mark { position: absolute; left: 0; width: 100%; text-align: center; }
  .brand-mark-front { top: 34px; }
  .brand-ring {
    display: block; margin: 0 auto; border-radius: 50%;
    border: 3px solid var(--olive); width: 96px; height: 96px;
  }
  .brand-name {
    font-family: "Oswald", "Arial Narrow", sans-serif; font-weight: 500;
    letter-spacing: 3px; text-transform: uppercase; color: var(--olive);
  }
  .brand-mark-front .brand-name { font-size: 19px; margin-top: 10px; }

  .brand-mark-back { top: 70px; }
  .brand-mark-back .brand-ring {
    width: 260px; height: 260px; border: 5px solid var(--white);
    display: flex; flex-direction: column; align-items: center; justify-content: center;
  }
  .brand-mark-back .brand-name { color: var(--white); font-size: 30px; line-height: 1.2; }

  .person { position: absolute; right: 360px; top: 230px; text-align: right; }
  .person-name { font-weight: 700; font-size: 21px; color: var(--olive); letter-spacing: .3px; line-height: 1; }
  .person-title { font-size: 18px; color: var(--grey-text); line-height: 1; margin-top: 3px; }

  .divider { position: absolute; left: 344px; top: 218px; width: 2px; height: 69px; background: var(--grey-text); }

  .contacts { position: absolute; left: 358px; top: 210px; list-style: none; }
  .contact { display: flex; align-items: center; height: 28px; font-size: 19px; color: var(--grey-text); }
  .contact-icon { width: 15px; height: 15px; margin-right: 10px; flex: none; }

  .address { position: absolute; left: 0; width: 100%; top: 306px; text-align: center; font-size: 19px; color: var(--grey-text); }
</style>
</head>
<body>

<section class="card card-front" aria-label="Card front">
  <svg class="front-wave" viewBox="0 0 689 394" aria-hidden="true">
    <path d="M0,330 Q344.5,406 689,330 L689,394 L0,394 Z" fill="var(--olive)"/>
    <path d="M62,338 Q344,380 627,338 Q344,392 62,338 Z" fill="var(--grey-swoosh)"/>
  </svg>

  <div class="brand-mark brand-mark-front">
    <span class="brand-ring"></span>
    <p class="brand-name">Vessolin Hair Studio</p>
  </div>

  <div class="person">
    <p class="person-name">MARCUS DELANE</p>
    <p class="person-title">Manager</p>
  </div>

  <span class="divider"></span>

  <ul class="contacts">
    <li class="contact">
      <svg class="contact-icon" viewBox="0 0 16 16" aria-hidden="true">
        <path d="M3.5 1.5l2.5 0 1 3.5-1.8 1.2a8 8 0 0 0 4.6 4.6L11 9l3.5 1v2.5c0 1-1 2-2 2A11 11 0 0 1 1.5 3.5c0-1 1-2 2-2z" fill="none" stroke="var(--olive)" stroke-width="1.5"/>
      </svg>
      248-613-4087
    </li>
    <li class="contact">
      <svg class="contact-icon" viewBox="0 0 16 16" aria-hidden="true">
        <circle cx="8" cy="8" r="6.5" fill="none" stroke="var(--olive)" stroke-width="2"/>
      </svg>
      @vessolinhairstudio
    </li>
    <li class="contact">
      <svg class="contact-icon" viewBox="0 0 16 16" aria-hidden="true">
        <g fill="none" stroke="var(--olive)" stroke-width="1.2">
          <circle cx="8" cy="8" r="6.5"/>
          <ellipse cx="8" cy="8" rx="3" ry="6.5"/>
          <path d="M1.5 8h13M2.5 4.8h11M2.5 11.2h11"/>
        </g>
      </svg>
      www.vessolinhairstudio.example
    </li>
  </ul>

  <p class="address">41782 Pelham Crest Rd, Farmington MI</p>
</section>

<section class="card card-back" aria-label="Card back">
  <div class="brand-mark brand-mark-back">
    <div class="brand-ring">
      <p class="brand-name">Vessolin</p>
      <p class="brand-name">Hair Studio</p>
    </div>
  </div>
</section>

</body>
</html>
```